High-End Print/Digital Ad for Unique Luxury Travel Company Required

Objective:
Design a compelling and visually striking advertisement that highlights our company’s unmatched luxury travel experiences. The ad should elevate our brand image, spark curiosity, and drive prospective clients to contact us.
Target Audience:
• Affluent individuals seeking extraordinary, tailor-made travel experiences
• Affluent, luxury, high-net-worth individuals looking for value, expertise, and white-glove service
• Professionals or retirees who appreciate unique, thoughtfully curated travel over mainstream tourism
Key Messages to Communicate:
• One-of-a-kind luxury travel: Once-in-a-lifetime experiences that are curated with creativity and meticulous attention to detail
• Exceptional service: White-glove, personalized planning from start to finish
• 38 years’ travel experience – expert knowledge of destinations, modes of travel, premium accommodations and well-established, meaningful industry connections.
• Highly trusted: Cruise line executives often say, “No one does what you do.”
Tone and Style:
• Elegant, luxurious, sophisticated
• Eye-catching, polished, and modern
• Professional but warm—conveys trust and credibility
• High-impact visuals (full-bleed imagery, custom graphics, or high-end photography)
Deliverables:
• One full-page print ad and digital ad
• Ready-to-print, high-resolution file + working file (PSD, AI, etc.)
Optional: Social media-optimized version or short motion-graphic variation (if designer offers it)
Inspiration & Visual Style Suggestions:
• Think Lumen Voyages, Harrow Pike Wanderer, Silver Quill, or Orvel Retreats ad styles
• Large, emotive imagery with elegant typography
• Clean layout that speaks luxury, clarity, and trust
Copy Direction (draft):
For those who’ve explored the world—and crave something beyond the ordinary.
Each journey is a masterfully curated experience, rich in detail, seamless in execution, and unforgettable in every way.
Founded in 1997, Tidewell Journeys is a unique travel company specializing in cruising, all-inclusive luxury properties, and tours world-wide for individuals, groups, and incentives.
We offer an exceptional range of services designed to ensure every journey is flawlessly executed and truly unforgettable.
Let us help you plan your next extraordinary adventure.
Note: You may refine the copy slightly based on layout or format needs.
Other Resources for References:
1. Website - www.tidewelljourneys-example.com

```html
<!DOCTYPE html>
<html lang="en">
<head>
<meta charset="utf-8">
<title>Tidewell Journeys – Luxury Travel Ad, Two Colourways</title>
<link href="https://fonts.googleapis.com/css2?family=Cinzel:wght@400;500&family=EB+Garamond:ital,wght@0,400;0,600;1,400&display=swap" rel="stylesheet">
<style>
  :root{
    --board:#9b9b9b;
    --navy:#0f3a62;
    --paper:#ffffff;
    --ink-light:#ffffff;
    --ink-dark:#2f2f36;
    --accent:#2c4f9e;
    --dots-light:rgba(255,255,255,.75);
    --dots-dark:#a9acb4;
  }
  *{box-sizing:border-box;margin:0;padding:0}
  html,body{width:1200px;height:842px;overflow:hidden}
  body{background:var(--board);position:relative;font-family:"EB Garamond",Georgia,serif}

  .ad{position:absolute;top:42px;width:538px;height:756px;overflow:hidden}
  .ad--navy{left:48px;background:var(--navy);color:var(--ink-light);--dots:var(--dots-light);--head:var(--ink-light)}
  .ad--paper{left:618px;background:var(--paper);color:var(--ink-dark);--dots:var(--dots-dark);--head:var(--accent)}
  .ad--paper .band{position:absolute;left:0;top:0;width:100%;height:310px;background:var(--navy)}

  .masthead{position:absolute;left:0;top:0;width:100%;text-align:center;color:var(--ink-light);font-family:"Cinzel",serif;text-transform:uppercase;font-weight:400}
  .masthead__kicker{position:absolute;top:50px;width:100%;font-size:13px;letter-spacing:-.2px}
  .masthead__title{position:absolute;top:72px;width:100%;font-size:22.5px;font-weight:400;letter-spacing:-.6px;white-space:nowrap}
  .masthead__sub{position:absolute;top:109px;width:100%;font-size:13.5px;letter-spacing:-.1px}
  .ad--paper .masthead{top:-5px}

  .divider{position:absolute;height:0;border-top:1.6px dotted var(--dots)}
  .divider--top-l{left:120px;top:155px;width:130px;border-color:var(--dots-light)}
  .divider--top-r{left:288px;top:155px;width:130px;border-color:var(--dots-light)}
  .emblem{position:absolute;left:261px;top:146px;width:18px;height:18px;border-radius:50%;border:1.5px solid var(--ink-light)}
  .ad--paper .divider--top-l,.ad--paper .divider--top-r{top:151px}
  .ad--paper .emblem{top:142px}

  .hero{position:absolute;left:53px;top:183px;width:431px;height:241px;
    background:linear-gradient(180deg,#f3c069 0%,#e9a55a 18%,#b98a7a 34%,#c9786a 48%,#8f6c5e 62%,#7a8a5a 78%,#d9b34a 100%)}
  .ad--paper .hero{left:47px;top:176px;width:437px;height:245px}

  .caption{position:absolute;top:427px;width:100%;text-align:center;font-size:8.6px}
  .divider--caption{left:135px;top:443px;width:268px}
  .ad--paper .divider--caption{left:132px;top:444px;width:272px}

  .col{position:absolute;top:461px;font-size:7.6px;line-height:10.6px}
  .col--intro p+p{margin-top:10.5px}
  .col--intro{left:53px;width:142px}
  .ad--paper .col--intro{left:47px;width:150px}
  .rule-v{position:absolute;top:462px;height:164px;width:0;border-left:1.6px dotted var(--dots)}
  .rule-v--a{left:198px}.rule-v--b{left:342px}
  .ad--paper .rule-v--a{left:194px}.ad--paper .rule-v--b{left:340px}

  .ship{position:absolute;left:207px;top:462px;width:127px;height:162px;background:var(--paper);padding:4px;box-shadow:0 6px 6px -4px rgba(0,0,0,.45)}
  .ship__fill{width:100%;height:100%;background:linear-gradient(180deg,#2f4f9a 0%,#5d77b5 30%,#aab6cf 52%,#d6c19a 62%,#4a4f62 74%,#2b3f66 100%)}
  .ad--paper .ship{left:204px;top:462px;width:128px;height:164px}

  .col--points{left:355px;width:130px;line-height:9.6px}
  .point+.point{margin-top:9px}
  .point__title{font-weight:600;font-size:7.8px;line-height:10px;color:var(--head)}
  .ad--paper .point__title{font-family:"Cinzel",serif;font-weight:400;font-size:7.4px;text-transform:uppercase;letter-spacing:-.3px}
  .point em{font-style:italic}

  .closing{position:absolute;top:646px;width:100%;text-align:center;font-size:8.6px}
  .divider--closing{left:207px;top:666px;width:124px}
  .ad--paper .closing{top:650px}
  .ad--paper .divider--closing{left:204px;top:670px;width:128px}

  .brand{position:absolute;top:681px;width:100%;display:flex;justify-content:center;align-items:center;gap:7px;font-family:"Cinzel",serif;font-size:15px;text-transform:uppercase;color:var(--ink-light)}
  .brand__dot{width:16px;height:16px;border-radius:50%;border:1.4px solid currentColor}
  .ad--paper .brand{top:685px;color:var(--accent)}
  .ad--paper .brand__dot{background:var(--accent);border:0}

  .contact{position:absolute;top:705px;width:100%;text-align:center;font-size:8.4px;white-space:nowrap}
  .contact b{font-weight:600}
  .ad--paper .contact{top:709px;display:flex;justify-content:center;gap:11px}
  .contact__item{display:inline-flex;align-items:center;gap:3px}
  .contact__item svg{width:8px;height:8px;fill:none;stroke:var(--ink-dark);stroke-width:1.3}
</style>
</head>
<body>

<section class="ad ad--navy">
  <header class="masthead">
    <p class="masthead__kicker">Four Decades of Inspiration</p>
    <h1 class="masthead__title">Once-in- a-Life Time Experience</h1>
    <p class="masthead__sub">Comes Your Way</p>
  </header>
  <div class="divider divider--top-l"></div><span class="emblem"></span><div class="divider divider--top-r"></div>

  <div class="hero" role="img" aria-label="Sunset panorama over a colourful mosaic park terrace and city skyline"></div>
  <p class="caption">Imagine what we could do if we shared our ideas</p>
  <div class="divider divider--caption"></div>

  <div class="col col--intro">
    <p>For those who’ve explored the world and crave something beyond the ordinary.</p>
    <p>Each journey is a masterfully curated experience, rich in detail, seamless in execution, and unforgettable in every way.</p>
    <p>Founded in 1997, Tidewell Journeys is a unique travel company specializing in cruising, all-inclusive luxury properties, and tours world-wide for individuals, groups, and incentives.</p>
    <p>We offer an exceptional range of services designed to ensure every journey is flawlessly executed and truly unforgettable.</p>
  </div>
  <div class="rule-v rule-v--a"></div>
  <figure class="ship"><div class="ship__fill" role="img" aria-label="Cruise ship at sea under a dramatic cloudy sky"></div></figure>
  <div class="rule-v rule-v--b"></div>

  <div class="col col--points">
    <div class="point"><p class="point__title">One-of-a-kind luxury travel</p><p>Once-in-a-lifetime experiences that are curated with creativity and meticulous attention to detail</p></div>
    <div class="point"><p class="point__title">Exceptional service</p><p>White-glove, personalized planning from start to finish</p></div>
    <div class="point"><p class="point__title">38 years’ travel experience</p><p>Expert knowledge of destinations, modes of travel, premium accommodations and well-established, meaningful industry connections.</p></div>
    <div class="point"><p class="point__title">Highly trusted</p><p>Cruise line executives often say, <em>“No one does what you do.”</em></p></div>
  </div>

  <p class="closing">Let us help you plan your next extraordinary adventure.</p>
  <div class="divider divider--closing"></div>
  <div class="brand"><span>Tidewell</span><span class="brand__dot"></span><span>Journeys</span></div>
  <p class="contact">toll-free 877.555.0142 | <b>p</b> 816.555.0187 | <b>e</b> travelplans@tidewelljourneys-example.com | tidewelljourneys-example.com</p>
</section>

<section class="ad ad--paper">
  <div class="band"></div>
  <header class="masthead">
    <p class="masthead__kicker">Four Decades of Inspiration</p>
    <h1 class="masthead__title">Once-in-a-Life Time Experience</h1>
    <p class="masthead__sub">Comes Your Way</p>
  </header>
  <div class="divider divider--top-l"></div><span class="emblem"></span><div class="divider divider--top-r"></div>

  <div class="hero" role="img" aria-label="Sunset panorama over a colourful mosaic park terrace and city skyline"></div>
  <p class="caption">Imagine what we could do if we shared our ideas</p>
  <div class="divider divider--caption"></div>

  <div class="col col--intro">
    <p>For those who’ve explored the world and crave something beyond the ordinary.</p>
    <p>Each journey is a masterfully curated experience, rich in detail, seamless in execution, and unforgettable in every way.</p>
    <p>Founded in 1997, Tidewell Journeys is a unique travel company specializing in cruising, all-inclusive luxury properties, and tours world-wide for individuals, groups, and incentives.</p>
    <p>We offer an exceptional range of services designed to ensure every journey is flawlessly executed and truly unforgettable.</p>
  </div>
  <div class="rule-v rule-v--a"></div>
  <figure class="ship"><div class="ship__fill" role="img" aria-label="Cruise ship at sea under a dramatic cloudy sky"></div></figure>
  <div class="rule-v rule-v--b"></div>

  <div class="col col--points">
    <div class="point"><p class="point__title">One-of-a-kind luxury travel</p><p>Once-in-a-lifetime experiences that are curated with creativity and meticulous attention to detail</p></div>
    <div class="point"><p class="point__title">Exceptional service</p><p>White-glove, personalized planning from start to finish</p></div>
    <div class="point"><p class="point__title">38 years’ travel experience</p><p>Expert knowledge of destinations, modes of travel, premium accommodations and well-established, meaningful industry connections.</p></div>
    <div class="point"><p class="point__title">Highly trusted</p><p>Cruise line executives often say, <em>“No one does what you do.”</em></p></div>
  </div>

  <p class="closing">Let us help you plan your next extraordinary adventure.</p>
  <div class="divider divider--closing"></div>
  <div class="brand"><span>Tidewell</span><span class="brand__dot"></span><span>Journeys</span></div>
  <div class="contact">
    <span class="contact__item">toll-free 877.555.0142</span>
    <span class="contact__item"><svg viewBox="0 0 10 10"><path d="M2 1.2l1.6 0 .7 2-1 .8a5 5 0 0 0 2.7 2.7l.8-1 2 .7v1.6c0 .5-.4.8-.9.8A7.6 7.6 0 0 1 1.2 2.1c0-.5.3-.9.8-.9z"/></svg>816.555.0187</span>
    <span class="contact__item"><svg viewBox="0 0 10 10"><rect x="1" y="2" width="8" height="6"/><path d="M1 2l4 3.3L9 2"/></svg>travelplans@tidewelljourneys-example.com</span>
    <span class="contact__item"><svg viewBox="0 0 10 10"><circle cx="5" cy="5" r="4"/><path d="M1 5h8M5 1c-2.2 2.4-2.2 5.6 0 8M5 1c2.2 2.4 2.2 5.6 0 8"/></svg>tidewelljourneys-example.com</span>
  </div>
</section>

</body>
</html>
```